Business Cards Needed for Innovative Healthcare Marketing Company

We are a marketing company focused on healthcare. Our company is all about rebranding yourself renewing your image and generating results. The phoenix stands for "reborn" or "rising" which we provide new brands for our clients we take their old brands and renew it with creativity and innovation. I am looking for a business card with color dimension. I have attached an example of a card I think has the look and feel of what I am trying to accomplish. I like that the card example has black and grey font colors, I like the font placement and the small logo, I really like the use of the colors on the right those are the colors of my logo. My logo is phoenix so maybe incorporating flames similar to that design. I would like the back a solid color maybe red with an opaque version of the logo and website. As a marketing company I am always open to creative liberty!

Target Market(s)

Doctors and business professionals.

Industry/Entity Type

Marketing

Contact Information for Business Card

Valcorne Health Care Marketing
Marla Tenwick- CEO
#(512)638-2974
email-marla@valcorne.com
website- valcorne.com

Font styles to use
Sans Serif

Colors
ec1f27
f37122
ffc214
fbed22
fbf289
f04a50

Requirements
Must have
• The logo and required information
Nice to have
• icons by the information
Should not have
• child like font

```html
<!DOCTYPE html>
<html lang="en">
<head>
<meta charset="utf-8">
<title>Valcorne Health Care Marketing – Business Card</title>
<link href="https://fonts.googleapis.com/css2?family=Raleway:wght@300;400&family=Open+Sans:wght@400;700&display=swap" rel="stylesheet">
<style>
  :root {
    --bg: #3b3b3b;
    --white: #ffffff;
    --crimson: #9e1c22;
    --deep-red: #7f1419;
    --red: #c2262c;
    --orange: #f37122;
    --amber: #f7a233;
    --brand-text: #b3343a;
    --name-text: #a8355a;
    --ink: #4a2a2a;
  }
  * { box-sizing: border-box; margin: 0; padding: 0; }
  html, body { width: 1200px; height: 950px; overflow: hidden; }
  body {
    background: var(--bg);
    font-family: "Open Sans", Arial, sans-serif;
    position: relative;
  }
  .card {
    position: absolute;
    left: 250px;
    width: 700px;
    height: 400px;
    border-radius: 26px;
    overflow: hidden;
  }
  .card--front { top: 55px; background: var(--white); }
  .card--back { top: 495px; background: var(--crimson); }

  .front-wave { position: absolute; inset: 0; }

  .brand {
    position: absolute;
    top: 70px;
    left: 0;
    width: 700px;
    display: flex;
    align-items: center;
    justify-content: center;
    gap: 18px;
  }
  .brand-mark {
    width: 54px; height: 54px;
    border-radius: 50%;
    background: var(--brand-text);
  }
  .brand-name {
    font-family: "Raleway", Arial, sans-serif;
    font-weight: 300;
    color: var(--brand-text);
    font-size: 34px;
    letter-spacing: 3px;
    text-transform: uppercase;
    line-height: 1.15;
  }

  .contact-block {
    position: absolute;
    left: 56px;
    top: 262px;
    color: var(--white);
  }
  .person-name {
    font-weight: 700;
    font-size: 22px;
    color: var(--name-text);
  }
  .person-role {
    font-size: 15px;
    margin-bottom: 10px;
  }
  .contact-list { list-style: none; position: absolute; left: 250px; top: 0; }
  .contact-list li {
    display: flex; align-items: center; gap: 10px;
    font-size: 14px; line-height: 28px;
  }
  .contact-icon { width: 18px; height: 18px; flex: none; }

  .back-site {
    position: absolute;
    left: 44px;
    top: 200px;
    transform: translate(-50%, -50%) rotate(90deg);
    transform-origin: center;
    color: var(--white);
    font-size: 14px;
    letter-spacing: 6px;
    white-space: nowrap;
    margin-left: 20px;
  }
  .back-brand {
    position: absolute;
    inset: 0;
    display: flex;
    align-items: center;
    justify-content: center;
    gap: 18px;
  }
  .back-brand .brand-mark { background: var(--white); width: 70px; height: 70px; opacity: .9; }
  .back-brand .brand-name { color: var(--white); font-size: 40px; }
</style>
</head>
<body>
  <section class="card card--front" aria-label="Business card front">
    <svg class="front-wave" viewBox="0 0 700 400" width="700" height="400" aria-hidden="true">
      <defs>
        <linearGradient id="bandFill" x1="0" y1="0" x2="1" y2="0">
          <stop offset="0" stop-color="#a51d24"/>
          <stop offset="0.35" stop-color="#d9492a"/>
          <stop offset="0.7" stop-color="#f37122"/>
          <stop offset="1" stop-color="#f7a233"/>
        </linearGradient>
      </defs>
      <path d="M0,200 C180,215 330,265 470,240 C570,222 640,190 700,170 L700,400 L0,400 Z" fill="#8a171c"/>
      <path d="M0,212 C180,232 330,285 470,262 C570,245 640,212 700,194 L700,400 L0,400 Z" fill="url(#bandFill)"/>
    </svg>

    <div class="brand">
      <span class="brand-mark"></span>
      <span class="brand-name">Valcorne<br>Health Care Marketing</span>
    </div>

    <div class="contact-block">
      <p class="person-name">Marla Tenwick</p>
      <p class="person-role">CEO</p>
      <ul class="contact-list">
        <li>
          <svg class="contact-icon" viewBox="0 0 18 18" aria-hidden="true"><circle cx="9" cy="9" r="9" fill="#fff"/><path d="M6 4.5l2 2-1 1.2a6 6 0 0 0 3.3 3.3l1.2-1 2 2-1.2 1.5C8.5 13.5 4.5 9.5 4.5 5.7z" fill="#7f1419"/></svg>
          (512)638-2974
        </li>
        <li>
          <svg class="contact-icon" viewBox="0 0 18 18" aria-hidden="true"><circle cx="9" cy="9" r="9" fill="#fff"/><rect x="4.5" y="5.5" width="9" height="7" fill="#7f1419"/><path d="M4.5 5.5L9 9.5l4.5-4" stroke="#fff" stroke-width="1" fill="none"/></svg>
          marla@valcorne.com
        </li>
        <li>
          <svg class="contact-icon" viewBox="0 0 18 18" aria-hidden="true"><circle cx="9" cy="9" r="9" fill="#fff"/><circle cx="9" cy="9" r="4.6" fill="none" stroke="#7f1419" stroke-width="1.3"/><path d="M4.4 9h9.2M9 4.4c-2 2.5-2 6.7 0 9.2M9 4.4c2 2.5 2 6.7 0 9.2" stroke="#7f1419" stroke-width="1" fill="none"/></svg>
          www.valcorne.com
        </li>
      </ul>
    </div>
  </section>

  <section class="card card--back" aria-label="Business card back">
    <p class="back-site">www.valcorne.com</p>
    <div class="back-brand">
      <span class="brand-mark"></span>
      <span class="brand-name">Valcorne</span>
    </div>
  </section>
</body>
</html>
```